Elegant & Eye-Catching Brochure- Photo Booth Rentals

We rent photo booths for weddings, sweet 16's, parties, mitzvah's, school and corporate events and we would like to create a vibrant and fun, yet professional brochure to be attractive to the entire spectrum of potential clients. The brochure will be the standard tri-fold style (8.5"x11") and will have 3 inside panels and 3 outside panels.

Ideally this brochure would be elegant, classy, and professional, but still vibrant and fun. We have many colorful images that convey the quality of our photos and options, we want to highlight that aspect, but also would like to maintain that we are a great selection for weddings. Thus we stress the classy yet fun aspect of this project. Also, it would be preferable to use legible and interesting, but clear fonts. Clean and less cluttered is also a plus, but by all means just do what you think looks best.

Attached are the photos that we have available and fit our goals. There is no need to use them all, but if possible please stress the great range of options and the lovely clean wedding shots. Blue, White, Silver and a splash of pink have been used in the past for our logo, site, business cards, and older brochures so those are the preferred colors for this brochure. This brochure should trend feminine. Most of our clients are brides and mothers so that should be taken into consideration, but only to a point so that we don't close ourselves off to anyone.

I am attaching a logo, some photos strips, single shots, and instructions on the actual wording. Please let me know if you need anything else. Thank you in advance.
Updates

Target Market(s)

most of our clients are female, but the brochure shouldn't be so feminine as to dissuade males from becoming clients

Industry/Entity Type

School

Colors
f9d9e8
ffffff
f0f0f0
86cae7

Requirements
Nice to have
• A way of fitting in a variety of colorful photos to highlight our range, but while still maintaining a clean and ordered look.

```html
<!DOCTYPE html>
<html lang="en">
<head>
<meta charset="utf-8">
<title>Seaside Snap Booths – Brochure</title>
<link href="https://fonts.googleapis.com/css2?family=Montserrat:wght@400;600;700&family=Parisienne&display=swap" rel="stylesheet">
<style>
:root{
  --paper:#ffffff;
  --panel:#c7e7ef;
  --pink:#f4a3c4;
  --blue:#1e8fd0;
  --script-blue:#3aa4d8;
  --ink:#454a4e;
  --grey:#6d7275;
  --frame:#7c8184;
  --photo-warm:#8a6a4d;
  --photo-teal:#2f95ad;
  --photo-dark:#3d3340;
}
*{margin:0;padding:0;box-sizing:border-box}
html,body{width:1200px;height:1000px;overflow:hidden;background:var(--paper)}
body{position:relative;font-family:'Montserrat',sans-serif;color:var(--ink)}
.brochure{position:absolute;left:105px;top:118px;width:990px;height:765px;background:var(--panel)}
.panel{position:absolute;top:0;width:330px;height:765px}
.panel--packages{left:0}
.panel--essentials{left:330px}
.panel--cover{left:660px}
.ribbon-band{position:absolute;left:0;top:65px;width:660px;height:13px;background:var(--pink)}
.title-plate{position:absolute;left:57px;top:16px;width:216px;height:56px;border:2px solid var(--frame);border-radius:30px 30px 6px 6px;background:var(--panel);font-family:'Parisienne',cursive;font-size:34px;color:var(--grey);text-align:center;line-height:50px}
.bow{position:absolute;background:var(--pink);border-radius:4px}
.package{position:absolute;left:18px;width:282px}
.package h3{font-family:'Parisienne',cursive;font-weight:400;font-size:19px;color:var(--script-blue);line-height:22px}
.list{list-style:none;font-size:10.8px;line-height:12.3px}
.list li::before{content:"• "}
.list li.wrap{padding-left:7px;text-indent:-7px}
.section-title{font-weight:700;font-size:13.5px;color:var(--blue);text-decoration:underline;letter-spacing:.2px}
.includes{position:absolute;left:18px;top:511px;width:280px}
.includes .list{margin-top:5px;line-height:12.6px}
.essentials{position:absolute;left:25px;top:89px;width:290px}
.essentials .list{margin-top:2px;line-height:13.6px}
.collage{position:absolute;left:22px;top:195px;width:285px;height:356px;background:#fff}
.shot{position:absolute}
.brand{position:absolute;text-align:center;font-family:'Montserrat',sans-serif;font-weight:600;color:var(--grey)}
.brand--small{left:43px;top:572px;width:244px;height:110px;font-size:17px}
.brand--cover{left:18px;top:242px;width:295px;height:106px;font-size:20px}
.brand .dot{display:block;margin:22px auto 10px;width:26px;height:26px;border-radius:50%;background:var(--grey)}
.contact{position:absolute;left:0;top:690px;width:330px;text-align:center;font-weight:700;font-size:12px;line-height:16.5px;color:var(--grey)}
.badge{position:absolute;left:5px;top:7px;width:68px;height:64px;background:#4aa2d6;z-index:2}
.cover-photo{position:absolute;left:0;width:330px}
.cover-band{position:absolute;left:0;top:667px;width:330px;height:13px;background:var(--pink)}
.tagline{position:absolute;left:0;top:724px;width:330px;text-align:center;font-family:'Parisienne',cursive;font-size:19px;white-space:nowrap;color:var(--grey)}
</style>
</head>
<body>
<main class="brochure">

  <section class="panel panel--packages">
    <div class="ribbon-band"></div>
    <div class="title-plate">Packages</div>
    <div class="bow" role="img" aria-label="Pink ribbon bow" style="left:105px;top:58px;width:60px;height:26px"></div>

    <div class="package" style="top:126px">
      <h3>The Happy Bride</h3>
      <ul class="list">
        <li>The Basic Package</li>
        <li>Scrapbook</li>
        <li class="wrap">Your Choice of Social Media Kiosk, Green Screen, or Specialty Booth Upgrade</li>
        <li>Print Per Person, per session</li>
      </ul>
    </div>
    <div class="package" style="top:223px">
      <h3>The Party Girl Package</h3>
      <ul class="list">
        <li>Basic Package</li>
        <li>Scrapbook</li>
        <li>Party Booth Upgrade</li>
        <li>Double Prints (2 strips per session becomes 4)</li>
      </ul>
    </div>
    <div class="package" style="top:308px">
      <h3>The Brand Builder Package</h3>
      <ul class="list">
        <li>Basic Package</li>
        <li>Social Media Kiosk</li>
        <li>Custom Branded Step &amp; Repeat Banner</li>
        <li>Branded Prints</li>
      </ul>
    </div>
    <div class="package" style="top:392px">
      <h3>The Perfect Package</h3>
      <ul class="list">
        <li>Basic Package</li>
        <li>Scrapbook</li>
        <li>Social Media Kiosk, Gatsby or Hollywood Upgrade</li>
        <li>Print Per Person</li>
        <li>100 2x6 Photo Frames</li>
        <li class="wrap">100 Photo Frame Placecard Inserts (designed by you or us)</li>
      </ul>
    </div>

    <div class="includes">
      <h2 class="section-title">EACH RENTAL PACKAGE COMES WITH:</h2>
      <ul class="list">
        <li>Your Choice of Classic or Open Booth.</li>
        <li>4 Hour Photo Booth Rental.</li>
        <li class="wrap">Professionally, Amazing, and Well Dressed Photo Booth Attendant.</li>
        <li class="wrap">High Quality Photography &amp; Lighting for the Finest Photos.</li>
        <li>(2) 2x6 Photo Strips per session.</li>
        <li class="wrap">Your Choice of Backdrop- over 10 colors to choose from.</li>
        <li class="wrap">Your Choice of Accent Curtain for Classic Booth rentals.</li>
        <li class="wrap">Your Choice of Caption &amp; Style to commemorate your event.</li>
        <li>Digital Copies of all images.</li>
        <li class="wrap">Access to a password protected gallery and free downloads for your guests.</li>
        <li>Prop Box with all the essentials.</li>
      </ul>
    </div>
  </section>

  <section class="panel panel--essentials">
    <div class="essentials">
      <h2 class="section-title">ESSENTIALS</h2>
      <ul class="list">
        <li>Double Prints per session</li>
        <li>Print per Person each session</li>
        <li>Plastic Sleeves</li>
        <li>2x6 acrylic frames &amp; 4x6 acrylic frames</li>
        <li>Placecard Inserts for your Frames</li>
        <li>Scrapbook</li>
      </ul>
    </div>

    <div class="collage">
      <div class="shot" role="img" aria-label="Photo: guest scrapbook on a table" style="left:3px;top:3px;width:186px;height:84px;background:linear-gradient(160deg,#c46a2e,#8a4a2a 45%,#2b5d66)"></div>
      <div class="shot" role="img" aria-label="Photo: bride and groom kissing" style="left:3px;top:91px;width:91px;height:86px;background:linear-gradient(135deg,#d8cfc8,#8b7f78 55%,#2f2f33)"></div>
      <div class="shot" role="img" aria-label="Photo strip: couple posing with party props" style="left:98px;top:91px;width:91px;height:260px;background:linear-gradient(#4a3d52,#6b4f6e 50%,#3a2f45)"></div>
      <div class="shot" role="img" aria-label="Photo: wedding couple against a teal backdrop" style="left:3px;top:181px;width:91px;height:170px;background:linear-gradient(150deg,var(--photo-teal),#7fb4bf 50%,#e4dcd6)"></div>
      <div class="shot" role="img" aria-label="Photo strip: wedding couple on teal backdrop" style="left:195px;top:3px;width:87px;height:262px;background:linear-gradient(var(--photo-teal),#3fa3bd 70%,#e9e9ef)"></div>
      <div class="shot" role="img" aria-label="Photo: bride and groom smiling" style="left:195px;top:269px;width:87px;height:82px;background:linear-gradient(135deg,#e4dfda,#9a9598 50%,#3f4247)"></div>
    </div>

    <div class="brand brand--small"><span class="dot"></span>Seaside Snap Booths</div>

    <div class="contact">
      <p>p: 555.014.2290</p>
      <p>e: hello@seasidesnap.com</p>
      <p>www.seasidesnap.com</p>
      <p>Maple Grove, NJ</p>
    </div>
  </section>

  <section class="panel panel--cover">
    <div class="badge" role="img" aria-label="Award badge"></div>
    <div class="cover-photo" role="img" aria-label="Photo: group of friends posing with party props" style="top:22px;height:216px;background:linear-gradient(135deg,#a49d99,#8c7775 45%,#5e4b52)"></div>
    <div class="brand brand--cover"><span class="dot"></span>Seaside Snap Booths</div>
    <div class="cover-photo" role="img" aria-label="Photo: bride and groom kissing" style="top:352px;height:315px;background:linear-gradient(160deg,#9c7a55,var(--photo-warm) 45%,#3b2c24)"></div>
    <div class="cover-band"></div>
    <div class="bow" role="img" aria-label="Pink ribbon bow" style="left:130px;top:658px;width:70px;height:30px"></div>
    <p class="tagline">Make Memories on Your Special Day</p>
  </section>

</main>
</body>
</html>
```